Willow Landing - Multifamily Development

Willow Landing is a Luxury Multifamily Development project located in Orange, NJ. This project will be completed in three phases with the first phase about 75% complete. Each phase will have a different name as follows
CEDAR Willow Landing
LANTERN Willow Landing
BRAMBLEWOOD Willow Landing
We are going to install a banner on the side of the first building which will act as advertising for all buildings. We will eventually need advertising that will be in the windows as well as marketing materials . We want the marketing for this project to be similar for all three phases. At the moment, we are starting with this first simple banner. Attached is a rough idea of the look as well as our color palette. If you feel the color palette is a little too monochrome, feel free to propose an accent color. You can also visit our website to see more info on our company as well as the project. www.tarnlv.com Finally, if you need AI files (ie. for the logo), we can send to you. Thanks..

```html
<!DOCTYPE html>
<html lang="en">
<head>
<meta charset="utf-8">
<title>Willow Landing – Now Leasing Banner</title>
<link rel="stylesheet" href="https://fonts.googleapis.com/css2?family=Montserrat:wght@500;800&family=Poppins:ital,wght@1,800&family=Roboto+Condensed:wght@500&display=swap">
<style>
  :root {
    --navy: #3f5170;
    --steel: #8a9ab3;
    --paper: #f5f6f9;
    --white: #ffffff;
    --scene: #b4bed8;
    --shadow-line: #c3cbda;
  }
  html, body {
    margin: 0;
    padding: 0;
    overflow: hidden;
    background: var(--navy);
  }
  .banner {
    position: relative;
    width: 1200px;
    height: 877px;
    background: var(--navy);
    overflow: hidden;
  }
  .panel {
    position: absolute;
    box-sizing: border-box;
  }
  .panel--brand { left: 94px; top: 81px; width: 329px; height: 136px; background: var(--steel); }
  .panel--now { left: 435px; top: 81px; width: 328px; height: 136px; background: var(--paper); }
  .panel--leasing { left: 776px; top: 81px; width: 329px; height: 136px; background: var(--paper); }
  .panel--name { left: 94px; top: 230px; width: 329px; height: 567px; background: var(--paper); }
  .panel--contact { left: 435px; top: 230px; width: 328px; height: 567px; background: var(--steel); }
  .panel--units { left: 776px; top: 230px; width: 329px; height: 567px; background: var(--paper); }

  .brand-name {
    position: absolute;
    inset: 0;
    display: flex;
    align-items: center;
    justify-content: center;
    font-family: "Montserrat", sans-serif;
    font-weight: 800;
    font-size: 56px;
    letter-spacing: 2px;
    color: var(--white);
  }
  .headline {
    position: absolute;
    inset: 0;
    display: flex;
    align-items: center;
    justify-content: center;
    font-family: "Poppins", sans-serif;
    font-style: italic;
    font-weight: 800;
    font-size: 60px;
    color: var(--navy);
    letter-spacing: -1px;
    padding-top: 6px;
  }

  .project-name {
    position: absolute;
    left: 98px;
    top: 40px;
    width: 130px;
    height: 455px;
    writing-mode: vertical-rl;
    transform: rotate(180deg);
    font-family: "Montserrat", sans-serif;
    font-weight: 500;
    font-size: 84px;
    line-height: 64px;
    letter-spacing: 3px;
    color: var(--navy);
    text-align: start;
    text-shadow: -4px 5px 0 var(--white), -5px 6px 0 var(--shadow-line);
  }
  .project-name span { display: block; }

  .contact-list {
    position: absolute;
    left: 45px;
    top: 207px;
    margin: 0;
    padding: 0;
    list-style: none;
    font-family: "Roboto Condensed", sans-serif;
    font-weight: 500;
    color: var(--white);
  }
  .contact-list li {
    display: flex;
    align-items: center;
    gap: 12px;
    font-size: 23px;
    height: 33px;
  }
  .contact-list li.contact-phone { font-size: 44px; height: 42px; }
  .contact-icon { width: 22px; height: 22px; flex: none; }

  .tagline {
    position: absolute;
    left: 36px;
    top: 404px;
    font-family: "Poppins", sans-serif;
    font-style: italic;
    font-weight: 800;
    font-size: 31px;
    line-height: 36px;
    color: var(--white);
    text-shadow: 2px 2px 0 var(--steel), 3px 3px 0 var(--white);
  }

  .unit-types {
    position: absolute;
    left: 32px;
    top: 205px;
    font-family: "Poppins", sans-serif;
    font-style: italic;
    font-weight: 800;
    font-size: 33px;
    line-height: 37px;
    color: var(--navy);
    text-shadow: 2px 2px 0 var(--white), 3px 3px 0 var(--shadow-line);
  }

  .lifestyle-scene {
    position: absolute;
    left: 0;
    bottom: 0;
    width: 329px;
    height: 155px;
  }
</style>
</head>
<body>
<main class="banner">
  <section class="panel panel--brand">
    <div class="brand-name">TARN</div>
  </section>
  <section class="panel panel--now">
    <div class="headline">NOW</div>
  </section>
  <section class="panel panel--leasing">
    <div class="headline">LEASING</div>
  </section>

  <section class="panel panel--name">
    <h1 class="project-name"><span>WILLOW</span><span>LANDING</span></h1>
  </section>

  <section class="panel panel--contact">
    <ul class="contact-list">
      <li>
        <svg class="contact-icon" viewBox="0 0 24 24" aria-hidden="true"><circle cx="12" cy="12" r="12" fill="#fff"/><path d="M12 5a4.5 4.5 0 0 0-4.5 4.5c0 3.4 4.5 8.5 4.5 8.5s4.5-5.1 4.5-8.5A4.5 4.5 0 0 0 12 5zm0 6.3a1.8 1.8 0 1 1 0-3.6 1.8 1.8 0 0 1 0 3.6z" fill="#8a9ab3"/></svg>
        CEDAR WILLOW LANDING
      </li>
      <li class="contact-phone">
        <svg class="contact-icon" viewBox="0 0 24 24" aria-hidden="true"><circle cx="12" cy="12" r="12" fill="#fff"/><path d="M8.3 6.5l2 2.3-1.2 1.6c.8 1.7 2 2.9 3.6 3.7l1.6-1.2 2.3 2-1.1 2.3c-4.6-.4-8.4-4.2-8.8-8.8z" fill="#8a9ab3"/></svg>
        555.014.2290
      </li>
      <li>
        <svg class="contact-icon" viewBox="0 0 24 24" aria-hidden="true"><circle cx="12" cy="12" r="12" fill="#fff"/><rect x="6" y="8" width="12" height="8.5" fill="none" stroke="#8a9ab3" stroke-width="1.5"/><path d="M6 8l6 5 6-5M6 16.5l4.5-4M18 16.5l-4.5-4" fill="none" stroke="#8a9ab3" stroke-width="1.3"/></svg>
        RENTALS@TARNLV.COM
      </li>
      <li>
        <svg class="contact-icon" viewBox="0 0 24 24" aria-hidden="true"><circle cx="12" cy="12" r="12" fill="#fff"/><path d="M8 6l9 6.5-4 .6 2.3 4-1.6.9-2.3-4-3 2.8z" fill="#8a9ab3"/></svg>
        WWW.TARNLV.COM
      </li>
    </ul>
    <p class="tagline">EXCEEEDING<br>EXPECTATIONS</p>
  </section>

  <section class="panel panel--units">
    <p class="unit-types">STUDIO,<br>1 &amp; 2<br>BEDROOM<br>APARTMENTS</p>
    <svg class="lifestyle-scene" viewBox="0 0 329 155" role="img" aria-label="Illustration of residents gathered around a table in a bright apartment lounge">
      <path d="M0 55 L120 50 C160 48 175 0 215 0 C245 0 255 25 258 60 C262 100 310 115 310 155 L0 155 Z" fill="var(--scene)"/>
    </svg>
  </section>
</main>
</body>
</html>
```